Business card for Eyelash extension salon in Beverly Hills,California USA

We need new business card for our salon in Beverly Hills. The salon name is 'Lashvera' . We would like to have...Business name: Lashvera Name of person: will provide later Address 4720 N.Alder Crest Ave Beverly Hills , CA 90210 Phone: will provide later (Text only) Web: www.lashverastudio.example Snapgrid icon, Circlebook icon follow us for seasonal campaign and news @lashverastudiolounge Design should look elegant, high-end, clean, simple, cohesive with my brand. Please refer my brand board. Business name color will be metallic bronzy color. Im thinking grey background or white background. Thanks

Target Market(s)

25-35. Gender neutral. People who are in Entertainment business industry.
This is High-end Eyelash extension salon in Beverly Hills

Industry/Entity Type

Beauty Salon

Contact Information for Business Card

Business name: Lashvera
Name of person: will provide later
Address 4720 N.Alder Crest Ave Beverly Hills , CA 90210
Phone: will provide later (Text only)
Web: www.lashverastudio.example
Snapgrid icon, Circlebook icon
follow us for seasonal campaign and news @lashverastudiolounge

Requirements
Must have
• Beautiful, elegant, clean and simple look but very attractive and modern
Should not have
• We don't like too clutter, too busy designs.

```html
<!DOCTYPE html>
<html lang="en">
<head>
<meta charset="utf-8">
<title>Lashvera Business Card</title>
<link href="https://fonts.googleapis.com/css2?family=Jost:wght@300;400;600&family=Source+Sans+3:wght@400;600&display=swap" rel="stylesheet">
<style>
  :root {
    --backdrop: #2b2b2d;
    --card: #141414;
    --card-edge: #1d1d1e;
    --bronze: #9a7452;
    --text-light: #d4d4d4;
    --text-dim: #a9a9a9;
    --rule: #3e3e40;
  }
  * { box-sizing: border-box; margin: 0; padding: 0; }
  html, body {
    width: 1200px; height: 900px; overflow: hidden;
    background: var(--backdrop);
  }
  .canvas {
    position: relative; width: 1200px; height: 900px;
    display: flex; flex-direction: column; align-items: center; justify-content: center; gap: 44px;
  }
  .card {
    position: relative; width: 630px; height: 360px;
    background: linear-gradient(180deg, var(--card-edge), var(--card));
    border-bottom: 9px solid var(--bronze);
    overflow: hidden;
  }
  /* Front */
  .card-front { display: flex; flex-direction: column; align-items: center; justify-content: center; }
  .brand-name {
    font-family: "Jost", sans-serif; font-weight: 300;
    font-size: 84px; letter-spacing: 2px; color: var(--bronze); line-height: 1;
  }
  .brand-location {
    margin-top: 14px;
    font-family: "Jost", sans-serif; font-weight: 400;
    font-size: 10px; letter-spacing: 3px; color: var(--bronze); text-transform: uppercase;
  }
  /* Back */
  .card-back { padding: 0; }
  .person-name {
    position: absolute; left: 56px; top: 112px;
    font-family: "Jost", sans-serif; font-weight: 600;
    font-size: 25px; letter-spacing: 1px; color: var(--bronze); text-transform: uppercase;
  }
  .divider {
    position: absolute; left: 320px; top: 92px; width: 1px; height: 96px; background: var(--rule);
  }
  .contact {
    position: absolute; left: 340px; top: 94px;
    font-family: "Source Sans 3", sans-serif; font-size: 15px; line-height: 1.45; color: var(--text-dim);
    list-style: none;
  }
  .contact li { display: flex; align-items: center; gap: 6px; }
  .contact svg { width: 12px; height: 12px; flex: none; }
  .social-row {
    position: absolute; left: 76px; right: 76px; top: 228px;
    display: flex; align-items: center; gap: 14px;
  }
  .social-row .rule { flex: 1; height: 1px; background: var(--rule); }
  .social-badge {
    display: flex; align-items: center; gap: 5px;
    font-family: "Source Sans 3", sans-serif; font-size: 12px; font-weight: 600; color: var(--text-light);
  }
  .social-badge .dot { width: 10px; height: 10px; border-radius: 50%; background: var(--text-dim); }
  .follow-line {
    position: absolute; left: 0; right: 0; top: 268px; text-align: center;
    font-family: "Source Sans 3", sans-serif; font-size: 15px; color: var(--text-light);
  }
  .follow-line .handle { font-weight: 600; }
</style>
</head>
<body>
<main class="canvas">
  <section class="card card-front">
    <div class="brand-name">Lashvera</div>
    <div class="brand-location">Beverly Hills</div>
  </section>

  <section class="card card-back">
    <h1 class="person-name">Marcus Ellery</h1>
    <div class="divider"></div>
    <ul class="contact">
      <li>4720 N.Alder Crest Ave</li>
      <li>Beverly Hills , CA 90210</li>
      <li>
        <svg viewBox="0 0 12 12" aria-hidden="true"><path d="M2.5 1h2l1 3-1.4 1a6 6 0 0 0 2.9 2.9l1-1.4 3 1v2A1.5 1.5 0 0 1 9.5 11 8.5 8.5 0 0 1 1 2.5 1.5 1.5 0 0 1 2.5 1z" fill="var(--bronze)"/></svg>
        044-987 654 321
      </li>
      <li>
        <svg viewBox="0 0 12 12" aria-hidden="true"><circle cx="6" cy="6" r="5" fill="none" stroke="var(--text-dim)" stroke-width="1.2"/><path d="M1 6h10M6 1c-2 2.5-2 7.5 0 10M6 1c2 2.5 2 7.5 0 10" fill="none" stroke="var(--text-dim)" stroke-width="1"/></svg>
        www.lashverastudio.example
      </li>
    </ul>
    <div class="social-row">
      <span class="rule"></span>
      <span class="social-badge"><span class="dot"></span>Circlebook</span>
      <span class="social-badge"><span class="dot"></span>Snapgrid</span>
      <span class="rule"></span>
    </div>
    <p class="follow-line">Follow us for seasonal campaign and news <span class="handle">@lashverastudiolounge</span></p>
  </section>
</main>
</body>
</html>
```